Ward Compass Business Card Design*

We need a business card design for our company Ward Compass. Our company is specialized in providing online consulting services regarding medical institutions, hospitals and doctors. We work with patients worldwide looking to choose between healthcare providers. We have a website you may use as a reference, where we list doctors and clinics worldwide. So we target Medical providers as well as patients worldwide.
Target Market(s)
Medical Providers and patients around the world
Industry/Entity Type
Medical
Contact Information for Business Card
Salwa Kettani
CEO
+90 612 348 2175
info@wardcompass.example
www.wardcompass.example
14 Annakhil 7 H.R.B. Rabat, Morocco
Requirements
Must have
- Company logo/name on one full side, personal info and smaller logo and company name on the other side.
Nice to have
- Smart and elegant design

```html
<!DOCTYPE html>
<html lang="en">
<head>
<meta charset="utf-8">
<title>Ward Compass Business Card</title>
<link rel="stylesheet" href="https://fonts.googleapis.com/css2?family=Montserrat:wght@400;600;700&family=Roboto:wght@400;500&display=swap">
<style>
  :root {
    --navy: #173a6a;
    --grey: #7b7b7b;
    --ink-soft: #8a8a8a;
    --paper: #ffffff;
    --backdrop: #d9d9d6;
  }
  * { box-sizing: border-box; margin: 0; padding: 0; }
  html, body {
    width: 1200px; height: 801px; overflow: hidden;
    background: var(--backdrop);
  }
  .sheet {
    position: relative; width: 1200px; height: 801px;
    display: flex; align-items: center; justify-content: center; gap: 60px;
  }
  .card {
    position: relative;
    width: 510px; height: 291px;
    background: var(--paper);
    border-bottom: 6px solid var(--navy);
    box-shadow: 0 14px 30px rgba(0,0,0,0.18);
  }
  .brand {
    display: flex; align-items: center;
    font-family: "Montserrat", sans-serif; font-weight: 600;
    color: var(--navy); letter-spacing: 0.04em; text-transform: uppercase;
    white-space: nowrap;
  }
  .brand-dot {
    border-radius: 50%; background: var(--navy); flex: none;
  }

  /* info side */
  .card-info .brand {
    position: absolute; left: 34px; top: 124px; font-size: 19px; gap: 10px;
  }
  .card-info .brand-dot { width: 30px; height: 30px; }
  .divider {
    position: absolute; left: 268px; top: 62px; width: 1px; height: 160px;
    background: var(--navy);
  }
  .details {
    position: absolute; left: 290px; top: 62px;
    font-family: "Roboto", sans-serif; color: var(--ink-soft);
    font-size: 11.5px; line-height: 1.45;
  }
  .person-name {
    font-family: "Montserrat", sans-serif; font-weight: 700;
    font-size: 15px; color: var(--navy); letter-spacing: 0.02em; text-transform: uppercase;
  }
  .person-name .surname { color: var(--grey); }
  .person-role {
    font-family: "Montserrat", sans-serif; font-weight: 700;
    font-size: 13px; color: var(--grey); margin-bottom: 10px;
  }
  .address { margin-bottom: 10px; }
  .contact-list { list-style: none; }
  .contact-list li { display: flex; align-items: center; gap: 7px; }
  .contact-list svg { width: 10px; height: 10px; flex: none; }
  .contact-list .accent { color: var(--navy); }

  /* logo side */
  .card-logo .brand {
    position: absolute; left: 50%; top: 50%; transform: translate(-50%, -50%);
    font-size: 30px; gap: 16px;
  }
  .card-logo .brand-dot { width: 52px; height: 52px; }
</style>
</head>
<body>
<main class="sheet">
  <section class="card card-info" aria-label="Business card, contact side">
    <div class="brand"><span class="brand-dot"></span>Ward Compass</div>
    <div class="divider"></div>
    <div class="details">
      <p class="person-name">Salwa <span class="surname">Kettani</span></p>
      <p class="person-role">CEO</p>
      <p class="address">14 Annakhil 7 H.R.B.<br>Rabat, Morocco</p>
      <ul class="contact-list">
        <li>
          <svg viewBox="0 0 10 10" aria-hidden="true"><path fill="var(--navy)" d="M2 0.5l1.6 2-1 1a6 6 0 0 0 3.9 3.9l1-1 2 1.6-1 1.5C4.5 9.5 0.5 5.5 0.5 1.5z"/></svg>
          +90 612 348 2175
        </li>
        <li>
          <svg viewBox="0 0 10 10" aria-hidden="true"><rect x="0.5" y="1.5" width="9" height="7" rx="1" fill="var(--navy)"/><path d="M1 2.5l4 3 4-3" stroke="#fff" stroke-width="1" fill="none"/></svg>
          info@wardcompass.example
        </li>
        <li>
          <svg viewBox="0 0 10 10" aria-hidden="true"><circle cx="5" cy="5" r="4.5" fill="var(--navy)"/><path d="M0.5 5h9M5 0.5c-2 2.5-2 6.5 0 9M5 0.5c2 2.5 2 6.5 0 9" stroke="#fff" stroke-width="0.7" fill="none"/></svg>
          <span>www.<span class="accent">wardcompass</span>.example</span>
        </li>
      </ul>
    </div>
  </section>

  <section class="card card-logo" aria-label="Business card, logo side">
    <div class="brand"><span class="brand-dot"></span>Ward Compass</div>
  </section>
</main>
</body>
</html>
```